New Business Card Design Project

We require a business card design for Vexalund, a newly established Indian company.
Our focus is on the development, manufacturing, and export of a diverse array of pharmaceutical products on a global scale. The card should convey a professional appearance, as our primary markets are in Africa, China, and Southeast Asian nations.
We envision a two-sided business card, with the reverse side dedicated to a logo set against a solid color or an elegantly designed pattern. The corners should be rounded. We would appreciate seeing both horizontal and vertical design options. We trust the designer to utilize their expertise in creating this design.

The content for the business card is included in the attached Word file.

Target Market(s)

Our primary markets are in Africa, China, and Southeast Asian, Latin America, Maldives, Sri Lanka

Industry/Entity Type

Pharmaceutical Manufacturing and Export

Contact Information for Business Card

Colors

Designer to choose colors to be used in the design.

Requirements
Must have
• The reverse side of the business card features solely the logo along with the tagline, "Remedies of Life."
Should not have
• The logo should not exceed two instances, encompassing both the front and back sides of the card.

```html
<!DOCTYPE html>
<html lang="en">
<head>
<meta charset="utf-8">
<title>Vexalund Business Card</title>
<link rel="stylesheet" href="https://fonts.googleapis.com/css2?family=Poppins:wght@400;700&display=swap">
<style>
  :root {
    --brand-blue: #27a8e0;
    --brand-red: #f0604d;
    --ink: #333333;
    --card: #ffffff;
    --backdrop: #2b2b2b;
  }
  * { margin: 0; padding: 0; box-sizing: border-box; }
  html, body { width: 1200px; height: 900px; overflow: hidden; }
  body {
    background: var(--backdrop);
    font-family: "Poppins", sans-serif;
    display: flex;
    flex-direction: column;
    align-items: center;
    justify-content: center;
    gap: 34px;
  }
  .card {
    position: relative;
    width: 700px;
    height: 400px;
    background: var(--card);
    border-radius: 26px;
    overflow: hidden;
  }
  .card-back {
    display: flex;
    align-items: center;
    justify-content: center;
  }
  .wordmark {
    display: flex;
    align-items: center;
    gap: 16px;
    color: var(--brand-blue);
    font-weight: 700;
  }
  .wordmark-dot {
    border-radius: 50%;
    background: var(--brand-red);
  }
  .card-back .wordmark { font-size: 74px; letter-spacing: 1px; }
  .card-back .wordmark-dot { width: 34px; height: 34px; }

  .card-front .wordmark {
    position: absolute;
    right: 58px;
    top: 78px;
    font-size: 44px;
    gap: 12px;
  }
  .card-front .wordmark-dot { width: 20px; height: 20px; }

  .identity {
    position: absolute;
    left: 64px;
    top: 128px;
  }
  .person-name {
    color: var(--brand-blue);
    font-weight: 700;
    font-size: 27px;
    line-height: 1.1;
  }
  .person-role, .person-company {
    color: var(--ink);
    font-size: 15px;
    line-height: 1.3;
  }
  .person-company { padding-left: 16px; }

  .divider {
    position: absolute;
    left: 64px;
    right: 50px;
    top: 216px;
    height: 1.5px;
    background: var(--brand-blue);
  }

  .contact-list {
    position: absolute;
    left: 84px;
    top: 232px;
    list-style: none;
  }
  .contact-list li {
    display: flex;
    align-items: center;
    gap: 10px;
    color: var(--ink);
    font-size: 15px;
    line-height: 1.75;
  }
  .contact-list svg { width: 14px; height: 14px; flex: none; }

  .address {
    position: absolute;
    right: 56px;
    top: 238px;
    text-align: right;
    color: var(--ink);
    font-size: 14px;
    line-height: 1.45;
    font-style: normal;
  }

  .edge-band {
    position: absolute;
    left: 0;
    bottom: 0;
    width: 700px;
    height: 40px;
  }
</style>
</head>
<body>

  <section class="card card-back" aria-label="Card reverse">
    <div class="wordmark">
      <span class="wordmark-dot"></span>
      <span class="wordmark-name">Vexalund</span>
    </div>
  </section>

  <section class="card card-front" aria-label="Card front">
    <div class="wordmark">
      <span class="wordmark-dot"></span>
      <span class="wordmark-name">Vexalund</span>
    </div>

    <div class="identity">
      <h1 class="person-name">Arjun K. Malhotra</h1>
      <p class="person-role">CEO</p>
      <p class="person-company">Vexalund</p>
    </div>

    <div class="divider"></div>

    <ul class="contact-list">
      <li>
        <svg viewBox="0 0 16 16" aria-hidden="true"><path fill="var(--brand-red)" d="M3.6 1.5l2.3 2.6-1.3 1.7c.9 2 2.5 3.6 4.6 4.6l1.7-1.3 2.6 2.3-1.2 2.1C7.3 14.6 1.4 8.7 1.5 3.1z"/></svg>
        <span>+919876501234</span>
      </li>
      <li>
        <svg viewBox="0 0 16 16" aria-hidden="true"><rect x="1" y="3" width="14" height="10" rx="1.5" fill="var(--brand-red)"/><path d="M1.5 4l6.5 5 6.5-5" fill="none" stroke="#fff" stroke-width="1.3"/></svg>
        <span>amalhotra@vexalund.com</span>
      </li>
      <li>
        <svg viewBox="0 0 16 16" aria-hidden="true"><circle cx="8" cy="8" r="7" fill="var(--brand-red)"/><path d="M1 8h14M8 1c-3 3.5-3 10.5 0 14M8 1c3 3.5 3 10.5 0 14" fill="none" stroke="#fff" stroke-width="1"/></svg>
        <span>www.vexalund.com</span>
      </li>
    </ul>

    <address class="address">
      12, Lotus Park, 422005<br>
      Nashik, India
    </address>

    <svg class="edge-band" viewBox="0 0 700 40" preserveAspectRatio="none" aria-hidden="true">
      <polygon points="0,26 448,26 438,40 0,40" fill="var(--brand-blue)"/>
      <polygon points="462,12 700,12 700,40 448,40" fill="var(--brand-red)"/>
    </svg>
  </section>

</body>
</html>
```